Private lender of mortgages and rent to own housing

need a website that reflects real estate especially mortgage lending and rent to own houses..
Sections as follows
Home About Types of mortgages Rent to own Contact us
Target Market(s)
consumers who require non traditonal mortgages
Industry/Entity Type
Mortgage
Coding
Coded - Design and coding required
Number of Pages Required
4 page
Font styles to use
Sans Serif
Colors
Designer to choose colors to be used in the design.
Requirements
Must have
- background pictures on pages. with nice picture on homepage of houses or a community
Nice to have
- contact us form i supplied a ink to

```html
<!DOCTYPE html>
<html lang="en">
<head>
<meta charset="utf-8">
<title>Harborline Lending Group</title>
<link href="https://fonts.googleapis.com/css2?family=Montserrat:wght@400;600;700&family=Open+Sans:wght@400;600&display=swap" rel="stylesheet">
<style>
:root{
  --purple:#3a2c8f;
  --purple-deep:#2a1f6e;
  --purple-light:#5646b0;
  --ink:#2b2b33;
  --text:#6b6b75;
  --grey-bg:#f1f1f4;
  --footer:#1d1d24;
  --footer-deep:#141419;
  --white:#ffffff;
}
*{box-sizing:border-box;margin:0;padding:0}
html,body{width:1200px;height:3156px;overflow:hidden}
body{font-family:"Open Sans",sans-serif;color:var(--text);background:var(--white);position:relative;font-size:14px;line-height:1.7}
h1,h2,h3,h4,.nav a,.btn,.brand{font-family:"Montserrat",sans-serif}
section,header,nav,footer{position:absolute;left:0;width:1200px}

.topbar{top:0;height:128px}
.contact-mini{position:absolute;left:112px;top:40px;font-size:13px;color:var(--ink);line-height:1.6}
.contact-mini div{display:flex;align-items:center;gap:8px}
.contact-mini svg{width:14px;height:14px;fill:var(--purple)}
.brand{position:absolute;left:0;right:0;top:46px;display:flex;justify-content:center;align-items:center;gap:12px;font-weight:700;font-size:22px;color:var(--purple);letter-spacing:1px}
.brand .mark{width:18px;height:18px;background:var(--purple)}
.search{position:absolute;right:112px;top:44px;width:210px;height:34px;border:1px solid #d9d9e0;display:flex;align-items:center;justify-content:space-between;padding:0 10px;font-size:12px;color:#a0a0aa}
.search svg{width:14px;height:14px;stroke:#8a8a94;fill:none;stroke-width:2}

.nav{top:128px;height:44px;background:var(--purple);display:flex;padding-left:112px}
.nav a{color:var(--white);text-decoration:none;font-size:13px;font-weight:600;padding:0 22px;line-height:44px}
.nav a.active{background:var(--purple-deep)}

.hero{top:172px;height:590px}
.hero-photo{position:absolute;inset:0;background:linear-gradient(180deg,#8fa6bd 0%,#a9b3bb 45%,#6f7a6b 80%,#4d5a46 100%)}
.hero-title{position:absolute;left:600px;width:420px;top:210px;text-align:center;color:var(--white)}
.hero-title h1{font-size:50px;font-weight:700;line-height:1.1;text-shadow:0 2px 8px rgba(0,0,0,.3)}
.btn{display:inline-block;background:var(--purple);color:var(--white);font-size:12px;font-weight:600;padding:9px 24px;border-radius:3px;letter-spacing:.5px}
.hero-title .btn{margin-top:18px}
.arrow{position:absolute;top:270px;width:30px;height:30px;background:rgba(0,0,0,.4);display:flex;align-items:center;justify-content:center}
.arrow svg{width:12px;height:12px;stroke:#fff;stroke-width:2.5;fill:none}
.arrow.prev{left:14px}.arrow.next{right:14px}

.section-title{text-align:center}
.section-title .rule{width:60px;height:4px;background:var(--purple);margin:0 auto 14px}
.section-title h2{font-size:34px;font-weight:700;color:var(--ink);letter-spacing:1px}

.rent{top:790px;height:400px;text-align:center}
.rent h3{color:var(--purple);font-size:18px;font-weight:600;margin:6px 0 22px}
.rent p{width:980px;margin:0 auto 12px;font-size:13px}
.rent .btn{margin-top:16px}

.welcome{top:1220px;height:480px}
.welcome-band{position:absolute;inset:0;background:linear-gradient(135deg,var(--purple-deep),var(--purple-light))}
.welcome-text{position:absolute;left:112px;top:110px;width:470px;color:#dcd8f2}
.welcome-text h2{color:var(--white);font-size:30px;font-weight:700;line-height:1.2;margin-bottom:22px}
.welcome-text p{font-size:13px;margin-bottom:14px}
.welcome-text .btn{background:transparent;border:1px solid #fff;margin-top:10px}
.welcome-photo{position:absolute;left:650px;top:105px;width:440px;height:270px;background:linear-gradient(135deg,#c9b79a,#8d8a86 55%,#e7e4df)}

.services{top:1740px;height:470px}
.service-row{display:flex;justify-content:center;gap:40px;margin-top:50px}
.service{width:220px;text-align:center}
.service .icon{width:100px;height:100px;border-radius:50%;background:var(--purple-deep);margin:0 auto 18px;display:flex;align-items:center;justify-content:center}
.service .icon svg{width:38px;height:38px;fill:#fff}
.service h4{font-size:14px;font-weight:700;color:var(--ink);margin-bottom:8px;letter-spacing:.5px}
.service p{font-size:12px;line-height:1.6}

.news{top:2220px;height:520px;background:var(--grey-bg);padding-top:50px}
.cards{display:flex;justify-content:center;gap:30px;margin-top:40px}
.card{width:330px;background:var(--white)}
.card .photo{height:160px}
.card .body{padding:16px 18px 20px}
.card .meta{font-size:11px;color:#9a9aa4;display:flex;gap:20px;margin-bottom:8px}
.card h4{font-size:13px;font-weight:700;color:var(--ink);margin-bottom:8px}
.card p{font-size:12px;line-height:1.6}

.footer{top:2740px;height:416px;background:var(--footer);color:#a9a9b3;font-size:12px}
.footer-cols{display:flex;padding:50px 112px 0;gap:60px}
.footer h4{color:var(--white);font-size:13px;font-weight:700;margin-bottom:18px;letter-spacing:.5px}
.f-about{width:320px}
.f-about .brand{position:static;justify-content:flex-start;color:var(--white);font-size:17px;margin:20px 0 14px}
.f-about .brand .mark{background:var(--white);width:14px;height:14px}
.subscribe{display:flex;margin-top:20px}
.subscribe span{width:200px;height:36px;border:1px solid #44444e;line-height:34px;padding-left:10px;color:#8a8a94}
.subscribe b{background:var(--purple);color:#fff;font-family:"Montserrat",sans-serif;font-size:11px;padding:0 16px;line-height:36px}
.f-contact{width:230px}
.f-contact li{display:flex;gap:10px;margin-bottom:12px;list-style:none}
.f-contact svg{width:13px;height:13px;fill:var(--purple-light);flex:none;margin-top:3px}
.f-links{width:140px}
.f-links li,.f-social li{list-style:none;margin-bottom:8px}
.f-social li{display:flex;align-items:center;gap:10px;margin-bottom:10px}
.f-social i{width:24px;height:24px;border-radius:50%;background:#34343d;display:block}
.copyright{position:absolute;left:0;right:0;bottom:0;height:56px;background:var(--footer-deep);text-align:center;line-height:56px;font-size:11px;color:#8a8a94}
</style>
</head>
<body>

<header class="topbar">
  <div class="contact-mini">
    <div><svg viewBox="0 0 24 24"><path d="M6.6 10.8a15 15 0 0 0 6.6 6.6l2.2-2.2c.3-.3.7-.4 1-.2 1.1.4 2.3.6 3.6.6.6 0 1 .4 1 1V20c0 .6-.4 1-1 1A17 17 0 0 1 3 4c0-.6.4-1 1-1h3.5c.6 0 1 .4 1 1 0 1.3.2 2.5.6 3.6.1.3 0 .7-.2 1z"/></svg>Call Us : +1 (555) 010-2470</div>
    <div><svg viewBox="0 0 24 24"><path d="M2 5h20v14H2zm2 2v.5l8 5 8-5V7z"/></svg>hello@harborlinelending.com</div>
  </div>
  <div class="brand"><span class="mark"></span>HARBORLINE LENDING GROUP</div>
  <div class="search">Search<svg viewBox="0 0 24 24"><circle cx="10" cy="10" r="6"/><path d="M15 15l6 6"/></svg></div>
</header>

<nav class="nav">
  <a class="active">HOME</a><a>ABOUT US</a><a>TYPES OF MORTGAGES</a><a>RENT TO OWN</a><a>CONTACT US</a>
</nav>

<section class="hero">
  <div class="hero-photo" role="img" aria-label="Smiling couple standing in front of their new suburban house"></div>
  <div class="arrow prev"><svg viewBox="0 0 12 12"><path d="M8 1L3 6l5 5"/></svg></div>
  <div class="arrow next"><svg viewBox="0 0 12 12"><path d="M4 1l5 5-5 5"/></svg></div>
  <div class="hero-title">
    <h1>HARBORLINE<br>LENDING GROUP</h1>
    <span class="btn">READ MORE</span>
  </div>
</section>

<section class="rent">
  <div class="section-title"><div class="rule"></div><h2>RENT TO OWN A HOME</h2></div>
  <h3>We Can Put You In Your Own Home Today</h3>
  <p>We know life sometimes delivers challenges and that a past credit setback or recent move can make a bank mortgage hard to reach. Maybe your income comes from contract work, or your down payment is still growing. Our rent to own program gives families a clear path to owning the home they live in, with part of each monthly payment set aside toward the purchase while you rebuild credit and savings.</p>
  <p>Instead of paying rent with nothing to show for it, you move into the house you choose today and lock in a future purchase price. Our team guides you through every step, from picking the property to arranging final financing, so the keys you hold now can become keys you own.</p>
  <span class="btn">READ MORE</span>
</section>

<section class="welcome">
  <svg class="welcome-band" width="1200" height="480" viewBox="0 0 1200 480" preserveAspectRatio="none" aria-hidden="true">
    <defs><linearGradient id="band" x1="0" y1="0" x2="1" y2="1"><stop offset="0" stop-color="#2a1f6e"/><stop offset="1" stop-color="#5646b0"/></linearGradient></defs>
    <polygon points="0,40 1200,0 1200,440 0,480" fill="url(#band)"/>
  </svg>
  <div class="welcome-text">
    <h2>WELCOME TO<br>HARBORLINE LENDING GROUP</h2>
    <p>Harborline Lending Group is a private lender of first, second and construction mortgages serving homeowners across the region. We offer flexible terms and fast answers to buyers that banks turn away.</p>
    <p>Our decisions look at the whole picture, not just a credit score, so self employed people, newcomers and families rebuilding credit can find a mortgage that fits their needs.</p>
    <span class="btn">READ MORE</span>
  </div>
  <div class="welcome-photo" role="img" aria-label="Happy couple holding up the keys to their new home"></div>
</section>

<section class="services">
  <div class="section-title"><div class="rule"></div><h2>OUR SERVICES</h2></div>
  <div class="service-row">
    <div class="service">
      <div class="icon"><svg viewBox="0 0 24 24"><text x="12" y="19" text-anchor="middle" font-family="Montserrat,sans-serif" font-weight="700" font-size="20" fill="#fff">$</text></svg></div>
      <h4>DOWN PAYMENT</h4>
      <p>We help you build a down payment over time so buying a home feels within reach.</p>
    </div>
    <div class="service">
      <div class="icon"><svg viewBox="0 0 24 24"><path d="M12 3l10 9h-3v9h-5v-6h-4v6H5v-9H2z"/></svg></div>
      <h4>HOUSEHOLD INCOME</h4>
      <p>Steady income from any source can support a mortgage plan that suits your budget.</p>
    </div>
    <div class="service">
      <div class="icon"><svg viewBox="0 0 24 24"><path d="M2 5h20v14H2zm2 3v2h16V8zm0 6v3h6v-3z"/></svg></div>
      <h4>CREDIT REPORT</h4>
      <p>Past credit issues do not close the door; we review your full story with care.</p>
    </div>
    <div class="service">
      <div class="icon"><svg viewBox="0 0 24 24"><path d="M2 11L22 3l-6 18-4-8zm10 2l3 5 4-12z"/></svg></div>
      <h4>SELECTING A HOUSE</h4>
      <p>Choose the home you love and we help you line up terms to make it yours.</p>
    </div>
  </div>
</section>

<section class="news">
  <div class="section-title"><div class="rule"></div><h2>LATEST NEWS</h2></div>
  <div class="cards">
    <article class="card">
      <div class="photo" role="img" aria-label="Advisor meeting with clients at a desk" style="background:linear-gradient(135deg,#b7c3d0,#6c7f94)"></div>
      <div class="body"><div class="meta"><span>March 21, 2017</span><span>No comments</span></div><h4>SED UT PERSPICIATIS UNDE OMNIS</h4><p>Simple tips for getting your finances ready before you apply for a home loan this spring.</p></div>
    </article>
    <article class="card">
      <div class="photo" role="img" aria-label="Hand holding house keys over a signed contract" style="background:linear-gradient(135deg,#e1c79a,#a27d4f)"></div>
      <div class="body"><div class="meta"><span>March 21, 2017</span><span>No comments</span></div><h4>SED UT PERSPICIATIS UNDE OMNIS</h4><p>How a rent to own agreement works and what to check before you sign the contract.</p></div>
    </article>
    <article class="card">
      <div class="photo" role="img" aria-label="Model house and paperwork on a table" style="background:linear-gradient(135deg,#d8c6b0,#8d7660)"></div>
      <div class="body"><div class="meta"><span>March 21, 2017</span><span>No comments</span></div><h4>SED UT PERSPICIATIS UNDE OMNIS</h4><p>Private mortgages explained: when they help and how to plan your move to bank financing.</p></div>
    </article>
  </div>
</section>

<footer class="footer">
  <div class="footer-cols">
    <div class="f-about">
      <div class="brand"><span class="mark"></span>HARBORLINE LENDING GROUP</div>
      <p>Private mortgages and rent to own homes for buyers who need a flexible path to ownership.</p>
      <div class="subscribe"><span>Enter Name</span><b>SUBSCRIBE</b></div>
    </div>
    <div class="f-contact">
      <h4>CONTACT US</h4>
      <ul>
        <li><svg viewBox="0 0 24 24"><path d="M12 2a7 7 0 0 0-7 7c0 5 7 13 7 13s7-8 7-13a7 7 0 0 0-7-7zm0 9.5A2.5 2.5 0 1 1 12 6.5a2.5 2.5 0 0 1 0 5z"/></svg><span>Harborline Lending Group<br>48 Cedar Row, Maple Bay</span></li>
        <li><svg viewBox="0 0 24 24"><path d="M6.6 10.8a15 15 0 0 0 6.6 6.6l2.2-2.2c.3-.3.7-.4 1-.2 1.1.4 2.3.6 3.6.6.6 0 1 .4 1 1V20c0 .6-.4 1-1 1A17 17 0 0 1 3 4c0-.6.4-1 1-1h3.5c.6 0 1 .4 1 1 0 1.3.2 2.5.6 3.6.1.3 0 .7-.2 1z"/></svg><span>Phone : +1 (555) 010-2470</span></li>
        <li><svg viewBox="0 0 24 24"><path d="M2 5h20v14H2zm2 2v.5l8 5 8-5V7z"/></svg><span>hello@harborlinelending.com</span></li>
      </ul>
    </div>
    <div class="f-links">
      <h4>QUICK LINKS</h4>
      <ul><li>Home</li><li>About Us</li><li>Types of mortgages</li><li>Rent to own</li><li>Contact us</li></ul>
    </div>
    <div class="f-social">
      <h4>SOCIAL MEDIA</h4>
      <ul><li><i></i>Chatterbox</li><li><i></i>Snapline</li><li><i></i>Circleup</li><li><i></i>Reelhouse</li></ul>
    </div>
  </div>
  <div class="copyright">Copyright © Harborline Lending Group 2017. All rights reserved.</div>
</footer>

</body>
</html>
```